Business Card Design Project

Business card based on attached logo

Todd Merrick
Todd@lorvantest.com
877-514-9073 ext. 318
Www.LorvanTest.com

Industry/Entity Type

Business

```html
<!DOCTYPE html>
<html lang="en">
<head>
<meta charset="utf-8">
<title>Lorvan Test — Business Card Set</title>
<link rel="stylesheet" href="https://fonts.googleapis.com/css2?family=Arimo:wght@400;700&display=swap">
<style>
  :root {
    --stage: #8a8c8f;
    --paper: #ffffff;
    --ink: #1f1d1e;
    --red: #e0262b;
    --red-deep: #b81e24;
    --charcoal: #2c2c2c;
    --charcoal-deep: #181818;
    --white: #ffffff;
  }
  * { box-sizing: border-box; margin: 0; padding: 0; }
  html, body { width: 1200px; height: 720px; overflow: hidden; }
  body {
    background: var(--stage);
    font-family: "Arimo", Arial, sans-serif;
    position: relative;
  }
  .card {
    position: absolute;
    width: 564px;
    height: 322px;
    overflow: hidden;
  }
  .card--front { left: 26px; top: 26px; background: var(--paper); border: 1px solid #6d6f72; }
  .card--red { left: 612px; top: 26px; background: linear-gradient(120deg, var(--red) 0%, var(--red-deep) 100%); }
  .card--white { left: 26px; top: 373px; background: var(--paper); border: 1px solid #6d6f72; }
  .card--dark { left: 612px; top: 373px; background: radial-gradient(ellipse at 50% 40%, var(--charcoal) 0%, var(--charcoal-deep) 100%); }

  .brand-name {
    font-weight: 700;
    letter-spacing: -1px;
    line-height: 1;
    white-space: nowrap;
  }
  .brand-name--front { position: absolute; left: 0; right: 0; top: 62px; text-align: center; font-size: 50px; color: var(--ink); }
  .brand-name--red { position: absolute; left: 34px; top: 34px; font-size: 70px; color: var(--white); }
  .brand-name--white { position: absolute; left: 0; right: 0; top: 108px; text-align: center; font-size: 66px; color: var(--ink); }
  .brand-name--dark { position: absolute; left: 0; right: 0; top: 108px; text-align: center; font-size: 66px; color: var(--white); }

  .name-band {
    position: absolute;
    left: 0; right: 0; top: 196px;
    height: 42px;
    border-top: 2px solid var(--ink);
    border-bottom: 2px solid var(--ink);
    padding: 3px 0;
  }
  .name-band__fill {
    height: 100%;
    background: linear-gradient(90deg, var(--red-deep) 0%, var(--red) 50%, var(--red-deep) 100%);
    display: flex; align-items: center; justify-content: center;
    color: var(--white); font-weight: 700; font-size: 20px;
  }
  .contact {
    position: absolute; left: 0; right: 0;
    display: flex; justify-content: center; align-items: center; gap: 18px;
    font-size: 16.5px; color: var(--ink);
  }
  .contact--phone { top: 258px; }
  .contact--links { top: 288px; }
  .contact__item { display: inline-flex; align-items: center; gap: 6px; }
  .contact__icon { width: 13px; height: 13px; }

  .web {
    position: absolute;
    font-size: 17px;
    letter-spacing: 3px;
  }
  .web--red { left: 34px; top: 290px; color: var(--white); }
  .web--white { left: 0; right: 0; top: 292px; text-align: center; color: var(--ink); }
  .web--dark { left: 0; right: 0; top: 292px; text-align: center; color: var(--white); }

  .accent-square {
    position: absolute;
    left: 420px; top: 170px;
    width: 112px; height: 112px;
    background: rgba(255, 255, 255, 0.14);
  }
</style>
</head>
<body>

  <section class="card card--front">
    <div class="brand-name brand-name--front">LORVAN TEST</div>
    <div class="name-band"><div class="name-band__fill">Todd Merrick</div></div>
    <div class="contact contact--phone">
      <span class="contact__item">
        <svg class="contact__icon" viewBox="0 0 16 16" aria-hidden="true"><path d="M3 1 L6 1 L7 5 L5 6 Q6 9.5 10 11 L11 9 L15 10 L15 13 Q14 15 12 15 Q2 13 1 3 Q1 1 3 1Z" fill="none" stroke="#1f1d1e" stroke-width="1.4"/></svg>
        877-514-9073 ext. 318
      </span>
    </div>
    <div class="contact contact--links">
      <span class="contact__item">
        <svg class="contact__icon" viewBox="0 0 16 16" aria-hidden="true"><rect x="1" y="4" width="14" height="10" fill="#1f1d1e"/><path d="M1 4 L8 10 L15 4" fill="none" stroke="#fff" stroke-width="1.2"/></svg>
        Todd@lorvantest.com
      </span>
      <span class="contact__item">
        <svg class="contact__icon" viewBox="0 0 16 16" aria-hidden="true"><circle cx="8" cy="8" r="6.5" fill="none" stroke="#1f1d1e" stroke-width="1.3"/><ellipse cx="8" cy="8" rx="3" ry="6.5" fill="none" stroke="#1f1d1e" stroke-width="1"/><line x1="1.5" y1="8" x2="14.5" y2="8" stroke="#1f1d1e" stroke-width="1"/></svg>
        www.lorvantest.com
      </span>
    </div>
  </section>

  <section class="card card--red">
    <div class="brand-name brand-name--red">LORVAN TEST</div>
    <div class="accent-square"></div>
    <div class="web web--red">www.lorvantest.com</div>
  </section>

  <section class="card card--white">
    <div class="brand-name brand-name--white">LORVAN TEST</div>
    <div class="web web--white">www.lorvantest.com</div>
  </section>

  <section class="card card--dark">
    <div class="brand-name brand-name--dark">LORVAN TEST</div>
    <div class="web web--dark">www.lorvantest.com</div>
  </section>

</body>
</html>
```